Our business name is Quillbrook Pty Ltd and we already have a logo. We would like the same colours that appear in our logo on our marketing material. I have attached our logo for colour consistency. We need a brochure designed that promotes our aerial photography and aerial imaging services. We'd like to use the brochure for electronic marketing purposes in an effort to attract a new client base. We are a new start up business so funds are fairly scarce. We use sophisticated UAV (unmanned aerial vehicle) or RPA - remotely piloted aircraft technology) that captures beautiful video and still images.
Our services are suitable for many types of industries and applications. We have identified at least 10 market sectors ranging, infrastructure inspections such as: gas pipelines, chemical and petrol storage facilities, pipeline and power line inspections, Archeological and geological surveys, vegetation mapping, wildlife surveys, agriculture and horticulture surveys, high end real estate, sport and event marketing. Our plan is to create a series of brochures (1) for each industry to help us market our business.

Our first brochure will focus on environmental management and compliance. We will target other industries down the track. These industries would see our service as helping them meet their compliance and auditing requirements.
We have a brochure that we put together containing words and some (very boring) format. As this will be one of a series of brochures, we'd like to colour code the industries for easy identification. (perhaps a green tab) in the corner to distinguish between our brochures. We have attached our boring brochure as a starting point. If we like the design there will be more work to follow. We want to be able to standardise the format for the other industries we will target. We anticipate needing another 6-8 brochures over the course of the next 2 months.

I have received questions regarding brochure size.  Apologies, I should have indicated in my posting previously.  The brochure is A3 landscape size so it can be folded in half to make 4 A4 pages.  We need to keep printing costs down so the content needs to be  within 4 pages.  I'm about to make some minor changes to the content to try to reduce the amount of text cause I can see this may be a problem.  Look forward to receiving your design. Thanking you in advance for your great work!

Re: Brochure Quillbrook Environmental Compliance and Monitoring Services

I have reduced the amount of text contained in the original version of the brochure making it more succinct and less wordy.  Could you use the least amount of space because we want to be able to use this brochure as both electric marketing and print based.  I have also included additional photos which will give you more to work with.  Thank you for your work in advance!  Regards Marta 

PLEASE NOTE - TEXT HAS BEEN UPDATED (REDUCED TEXT IN BROCHURE). COULD YOU REFER TO VERSION 2 OF QUILLBROOK ENVIRONMENTAL COMPLIANCE AND MONITORING SERVICES BROCHURE UPDATED FRIDAY 17TH.

Thanks Marta 

Hi talented designers working on the Quillbrook Brochure for Environmental Compliance and Monitoring.  I have been asked to upload the EPS version of Quillbrook Logo.  I have just done so.

Regards
Marta 

Hi all, to assist you with the design concept. I feel I need to clarity a number of points.  We are a new technology driven business.  No one else is conducting environmental surveys using this type of sophisticated equipment. We are in the business of providing clients with visual data (aerial images). Could you include grab lines in the brochure that draws attention to this. We us state of the art technology to produce high quality images efficiently, safely and economically. 

Thank you
Marta

Reason: We need additional time to receive and review designs.

Reason: Need additional time to communicate with designers and to review changes. Thank you Marta

I have extended the project date a few days. I have been incredibly impressed by the quality of your work and thank you all for your efforts.  I am waiting on a few revisions by a number of designers and look forward to receiving these changes.  We are close to completion.  Thanking you all again. Marta 

We are targeting a wide range of industry sectors. Specifically, looking at targeting large engineering type consultancies, corporations, government agencies, auditing bodies. Typically, targeting the professional sector who use data to confirm, monitor and make better decisions.

We want the brochure design to be contemporary and modern which reflects what our business does. We use state of the art unmanned aerial technology to capture brilliant visual images and video. So we want our brochure to reflect that we're leaders in the field offering something different - cutting edge approach. I have additional photos that show vegetation mapping, wildlife surveys, agriculture and horticulture applications. Our services would benefit any business that uses visual data to help them make better, more informed decisions.

Business

Serif
Sans Serif

• We would like you to include photo of the UAV equipment/technology shots. This is new technology so we must also educate our clients on what our technology is capable of doing. We are offering a service that is very different so we want to be able to convey the true benefits of our services such as safety, efficiency, cost saving, reliability. We would like to convey these key themes. Credible data enables businesses to make better, faster decisions.
• We are essentially providing visual data in the form of high definition photos and videos. For this particular sector, data could be used for compliance or auditing purposes, planning, measuring, monitoring, evaluating, assessing, marketing. Could you please include these words in the brochure as they capture our service provision. Please note the red photo is infrared images.

```html
<!DOCTYPE html>
<html lang="en">
<head>
<meta charset="utf-8">
<title>Quillbrook brochure spread</title>
<link href="https://fonts.googleapis.com/css2?family=Questrial&family=Cinzel:wght@500&display=swap" rel="stylesheet">
<style>
:root{
  --bg:#e9e9e7;
  --paper:#f4f6f9;
  --paper-edge:#dde3ea;
  --green:#8cc63f;
  --blue:#00a9e6;
  --sky:#bfe3f7;
  --grey:#8c8d8f;
  --ink:#3a3a3a;
  --white:#ffffff;
}
*{margin:0;padding:0;box-sizing:border-box}
html,body{width:1200px;height:802px;overflow:hidden;background:var(--bg)}
body{font-family:"Questrial",sans-serif;color:var(--ink)}
.spread{position:absolute;left:20px;top:26px;width:1160px;height:750px;display:flex;box-shadow:0 2px 8px rgba(0,0,0,.18)}
.page{position:relative;width:580px;height:750px;overflow:hidden;background:radial-gradient(ellipse at 50% 40%,var(--paper) 40%,var(--paper-edge) 100%)}
.page--inside{border-right:1px solid #cfd5dc}
.page-art{position:absolute;inset:0;width:580px;height:750px}
.section-tab{position:absolute;left:41px;top:85px;width:134px;height:28px;background:var(--blue);border-radius:8px 14px 14px 8px;color:var(--white);font-family:"Cinzel",serif;font-size:19px;line-height:28px;padding-left:12px;letter-spacing:.5px}
.staff-copy{position:absolute;left:47px;top:133px;width:486px;font-size:9.2px;line-height:11.3px}
.staff-copy p{text-align:justify;margin-bottom:11px}
.acts{list-style:none;margin:-3px 0 13px 32px}
.acts li{line-height:15.1px;position:relative;padding-left:7px}
.acts li::before{content:"";position:absolute;left:-1px;top:5px;width:4px;height:4px;border-radius:50%;background:var(--blue)}
.more-link{position:absolute;right:46px;top:490px;color:var(--blue);font-weight:bold;font-size:11.5px}
.brand-badge{position:absolute;left:22px;top:555px;width:160px;height:46px;background:var(--white);border-radius:14px;display:flex;align-items:center;justify-content:center;color:var(--blue);font-size:19px;letter-spacing:.3px}
.contact{position:absolute;left:25px;color:var(--white);font-size:9.5px;line-height:11px;display:flex;gap:6px;align-items:flex-start}
.contact svg{flex:none;margin-top:1px}
.contact--phone{font-size:11.5px;font-weight:bold}
.contact--web{font-size:15px}
.photo{position:absolute}
.brand-title{position:absolute;left:30px;top:88px;color:var(--blue);font-size:46px;letter-spacing:-1px;line-height:50px}
.brand-tagline{position:absolute;left:124px;top:139px;color:var(--blue);font-size:11px;letter-spacing:.3px}
.web-footer{position:absolute;right:18px;top:713px;color:var(--white);font-size:15px;display:flex;gap:5px;align-items:center}
</style>
</head>
<body>
<div class="spread">

  <section class="page page--inside">
    <svg class="page-art" viewBox="0 0 580 750" aria-hidden="true">
      <path d="M0,0 L150,0 C80,20 25,50 0,98 Z" fill="var(--green)"/>
      <path d="M0,532 C130,512 320,560 580,694 L580,750 L0,750 Z" fill="var(--grey)"/>
      <path d="M20,510 C190,500 360,555 560,664" fill="none" stroke="var(--white)" stroke-width="5" opacity=".8"/>
      <path d="M170,508 C320,520 430,580 560,664" fill="none" stroke="var(--blue)" stroke-width="3"/>
    </svg>

    <h2 class="section-tab">Our staff</h2>

    <div class="staff-copy">
      <p>Dan Whitcombe is Quillbrook's Chief UAV Pilot and Environmental Scientist. He is the only environmental scientist in Australia accredited by AVRA to use UAV technology for commercial purposes.</p>
      <p>Dan has over 20-years' experience in the resource management sector including 15 years in professional services providing environmental consultancy to a range of clients across many industry sectors. He also provides advice on relevant national and state legislation and policy. For example in Victoria:</p>
      <ul class="acts">
        <li>Environment Protection and Biodiversity Conservation Act 1999</li>
        <li>Flora and Fauna Guarantee&nbsp; Act&nbsp; 1988</li>
        <li>Mineral Resources (Sustainable Development) Act 1990</li>
        <li>Climate Change and Environment Protection Amendment Act 2012</li>
        <li>Wildlife Act 1975</li>
        <li>National Parks Act 1975</li>
        <li>Environmental Effect Act 1978</li>
        <li>Planning and Environment Act 1987</li>
        <li>Catchment and Land Protection Act 1994</li>
        <li>Aboriginal Heritage Act 2006</li>
        <li>Native Vegetation Framework</li>
      </ul>
      <p>Marta Lindqvist is Quillbrook's Business Development Manager. Marta has spent a considerable part of her career in the corporate sector where she worked for leading global companies such as Aeroline, Kaneda and Norbridge Systems. She has held management roles in human resources, industrial relations and organisational development. Marta has a strong focus on project management /client relations, OH&amp;S, audits, compliance and quality management systems. She is one of few people in Australia to be accredited by Kaneda Motor Corporation (Japan) as a Total Quality Management Facilitator &amp; Assessor. Marta has spent a considerable part of her career supporting Engineering and Maintenance functions.</p>
    </div>

    <p class="more-link">Find out more at www.quillbrook.com.au</p>

    <svg class="photo" style="left:272px;top:537px" width="244" height="182" role="img" aria-label="Infrared photograph of a grass field under stormy sky">
      <defs><linearGradient id="ir" x1="0" y1="0" x2="0" y2="1"><stop offset="0" stop-color="#5a4a66"/><stop offset=".45" stop-color="#8a6f8e"/><stop offset=".55" stop-color="#a04a86"/><stop offset="1" stop-color="#7a2d64"/></linearGradient></defs>
      <ellipse cx="122" cy="91" rx="122" ry="91" fill="url(#ir)"/>
    </svg>

    <div class="brand-badge">QUILLBROOK</div>

    <div class="contact" style="top:612px">
      <svg width="8" height="11" viewBox="0 0 8 11"><path d="M4,0 A4,4 0 0 1 8,4 C8,7 4,11 4,11 C4,11 0,7 0,4 A4,4 0 0 1 4,0Z" fill="var(--white)"/><circle cx="4" cy="4" r="1.5" fill="var(--grey)"/></svg>
      <span>1111 Abcdef ghijkl<br>mnopqrst 111<br>uvwxyz 11111</span>
    </div>
    <div class="contact contact--phone" style="top:668px">
      <svg width="10" height="10" viewBox="0 0 10 10"><circle cx="5" cy="5" r="4.4" fill="none" stroke="var(--white)"/><path d="M3.3,2.6 L4.3,3.8 L3.8,4.4 C4.2,5.2 4.8,5.8 5.6,6.2 L6.2,5.7 L7.4,6.7 L6.8,7.5 C4.8,7.3 2.7,5.2 2.5,3.2Z" fill="var(--white)"/></svg>
      <span>(000) 123-4567</span>
    </div>
    <div class="contact" style="top:689px">
      <svg width="10" height="10" viewBox="0 0 10 10"><rect x="1" y="4" width="8" height="5" fill="none" stroke="var(--white)"/><rect x="3" y="1" width="4" height="3" fill="none" stroke="var(--white)"/></svg>
      <span>(000) 123-4567</span>
    </div>
    <div class="contact" style="top:712px">
      <svg width="10" height="8" viewBox="0 0 10 8"><rect x=".5" y=".5" width="9" height="7" fill="none" stroke="var(--white)"/><path d="M.5,.5 L5,4.5 L9.5,.5" fill="none" stroke="var(--white)"/></svg>
      <span>info@quillbrook.co.au</span>
    </div>
    <div class="contact contact--web" style="top:727px">
      <svg width="13" height="13" viewBox="0 0 12 12" style="margin-top:3px"><circle cx="6" cy="6" r="5.4" fill="none" stroke="var(--white)"/><ellipse cx="6" cy="6" rx="2.4" ry="5.4" fill="none" stroke="var(--white)"/><path d="M.6,6 H11.4 M1.5,3.3 H10.5 M1.5,8.7 H10.5" stroke="var(--white)"/></svg>
      <span>www.quillbrook.com.au</span>
    </div>
  </section>

  <section class="page page--cover">
    <svg class="page-art" viewBox="0 0 580 750" aria-hidden="true">
      <path d="M141,24 C200,0 280,-2 340,30 C420,75 470,115 580,122 L580,0 L150,0 Z" fill="var(--green)"/>
      <circle cx="288" cy="428" r="178" fill="var(--sky)"/>
      <path d="M0,694 C60,700 110,702 150,704 C110,720 75,738 55,750 L0,750 Z" fill="var(--grey)"/>
      <path d="M55,750 C160,680 380,690 580,638 L580,750 Z" fill="var(--blue)"/>
    </svg>

    <h1 class="brand-title">QUILLBROOK</h1>
    <p class="brand-tagline">AERIAL &amp; SPATIAL IMAGING</p>

    <svg class="photo" style="left:208px;top:172px" width="160" height="160" role="img" aria-label="Aerial photo of a winding creek through green wetland"><circle cx="80" cy="80" r="80" fill="#7a9a4a"/></svg>
    <svg class="photo" style="left:374px;top:255px" width="160" height="160" role="img" aria-label="Aerial photo of a murky dam with vegetation"><circle cx="80" cy="80" r="80" fill="#8f9a5a"/></svg>
    <svg class="photo" style="left:374px;top:436px" width="160" height="160" role="img" aria-label="Aerial photo of shrubs and scattered trees"><circle cx="80" cy="80" r="80" fill="#6f8a48"/></svg>
    <svg class="photo" style="left:208px;top:517px" width="160" height="160" role="img" aria-label="Aerial photo of flowering bushes on grassland"><circle cx="80" cy="80" r="80" fill="#84a65a"/></svg>
    <svg class="photo" style="left:44px;top:437px" width="160" height="160" role="img" aria-label="Aerial photo of trees casting shadows over a track"><circle cx="80" cy="80" r="80" fill="#6e9448"/></svg>
    <svg class="photo" style="left:44px;top:255px" width="160" height="160" role="img" aria-label="Low aerial photo of crop fields beside a lake"><defs><linearGradient id="crop" x1="0" y1="0" x2="0" y2="1"><stop offset="0" stop-color="#c7d3d8"/><stop offset=".4" stop-color="#8a9a70"/><stop offset="1" stop-color="#4f8a3e"/></linearGradient></defs><circle cx="80" cy="80" r="80" fill="url(#crop)"/></svg>
    <svg class="photo" style="left:191px;top:378px" width="190" height="100" role="img" aria-label="Photo of the quadcopter UAV"><defs><radialGradient id="uav"><stop offset="0" stop-color="#3a3a3c"/><stop offset=".7" stop-color="#555658" stop-opacity=".8"/><stop offset="1" stop-color="#555658" stop-opacity="0"/></radialGradient></defs><ellipse cx="95" cy="50" rx="95" ry="50" fill="url(#uav)"/></svg>

    <p class="web-footer">
      <svg width="13" height="13" viewBox="0 0 12 12"><circle cx="6" cy="6" r="5.4" fill="none" stroke="var(--white)"/><ellipse cx="6" cy="6" rx="2.4" ry="5.4" fill="none" stroke="var(--white)"/><path d="M.6,6 H11.4 M1.5,3.3 H10.5 M1.5,8.7 H10.5" stroke="var(--white)"/></svg>
      www.quillbrook.com.au
    </p>
  </section>

</div>
</body>
</html>
```